Larkspur Talent IT Recruiting firm needs a business card design for Recruiters, Sourcers, and Account

We need business cards that allow us to change all contact info, names, titles (Recruiter, Sourcer, Account Manager, Director, CEO, etc) per person since we have three offices, in three cities, Phoenix, Austin, and Las Vegas. We do recruiting and contractors for IT positions (Developers, Architects, Software Engineers, Security Engineers, Help Desk, DBAs, PMs, Scrum Masters, etc.) Our client companies are very diverse from Meridian 100 to silicone Valley type start-ups.

So, while we what hip, techie, and quirky, it still needs to be professional. Primary color we use is blue, with silver as a secondary color.

Target Market(s)

IT, Technology

Industry/Entity Type

Business

Contact Information for Business Card

Company name: Larkspur Talent, Inc.
Website: www.larkspurtalent.example
Logos for Careerloop, Blipster, and Myriada

Name, Title, Office Number, Cell Number, email

Font styles to use
Serif
Sans Serif

Colors
0455a3
d5d5d5

Requirements
Nice to have
• The grey I selected below is not necessary - but, would like silver included. I included a card design (File 3: LTI early trial example.jpg) that I had started on. It's very rough, and not quite what we're looking for, but what we did like is the logo, big, maybe a bit faded, off center, goes out of frame, etc. Still looking for other ideas - you are the pros! But, just an idea of a design element we liked.

```html
<!DOCTYPE html>
<html lang="en">
<head>
<meta charset="utf-8">
<title>Larkspur Talent — Business Cards</title>
<link rel="stylesheet" href="https://fonts.googleapis.com/css2?family=Marcellus&family=Lato:wght@400;700&display=swap">
<style>
  :root {
    --brand-blue: #0455a3;
    --sky-blue: #2ea8ef;
    --bright-blue: #1b7fe6;
    --silver: #d5d5d5;
    --ink: #1c1c1c;
    --card-dark: #17181a;
    --card-light: #f6f6f6;
    --page: #e9e9eb;
    --muted: #9a9a9a;
  }
  * { box-sizing: border-box; margin: 0; padding: 0; }
  html, body {
    width: 1200px; height: 900px; overflow: hidden;
    background: var(--page);
    font-family: "Lato", Arial, sans-serif;
  }
  .sheet {
    width: 1200px; height: 900px;
    display: flex; flex-direction: column; align-items: center; justify-content: center; gap: 40px;
  }
  .card {
    position: relative; width: 700px; height: 400px; overflow: hidden;
    border-radius: 4px;
    box-shadow: 0 10px 26px rgba(0,0,0,.18);
  }
  .card__art { position: absolute; inset: 0; }

  .wordmark {
    font-family: "Marcellus", Georgia, serif;
    font-size: 34px; letter-spacing: 3px; line-height: 1;
    display: flex; align-items: center; gap: 12px;
    white-space: nowrap;
  }
  .wordmark__dot { width: 28px; height: 28px; border-radius: 50%; background: var(--bright-blue); flex: none; }
  .tagline {
    font-family: "Marcellus", Georgia, serif;
    font-size: 14px; letter-spacing: 3px; text-transform: uppercase;
    white-space: nowrap;
  }

  /* Back card */
  .card--back { background: var(--card-dark); }
  .card--back .brand { position: absolute; left: 270px; top: 96px; }
  .card--back .wordmark { color: var(--silver); }
  .card--back .tagline { color: var(--muted); margin-top: 22px; padding-left: 40px; }
  .card--back .website {
    position: absolute; left: 340px; top: 232px;
    color: var(--sky-blue); font-size: 20px; letter-spacing: .5px;
  }
  .socials { position: absolute; left: 340px; top: 280px; display: flex; gap: 16px; list-style: none; }
  .socials li { display: flex; align-items: center; gap: 6px; color: var(--muted); font-size: 12px; }
  .socials li::before { content: ""; width: 22px; height: 22px; border-radius: 50%; background: #3a3b3e; }

  /* Front card */
  .card--front { background: var(--card-light); }
  .card--front .brand { position: absolute; left: 60px; top: 74px; }
  .card--front .wordmark { color: var(--ink); }
  .card--front .tagline { color: #333; margin-top: 28px; }
  .contact { position: absolute; right: 300px; top: 200px; text-align: right; color: var(--ink); }
  .contact__name { font-size: 26px; font-weight: 700; }
  .contact__title { font-size: 18px; color: var(--sky-blue); margin-top: 2px; }
  .contact__lines { list-style: none; margin-top: 22px; font-size: 20px; line-height: 1.3; }
  .contact__lines li { display: flex; justify-content: flex-end; align-items: center; gap: 6px; white-space: nowrap; }
  .contact__lines svg { width: 13px; height: 13px; fill: var(--bright-blue); }
  .contact__lines .email { margin-right: -90px; margin-top: 14px; font-size: 22px; }
</style>
</head>
<body>
<main class="sheet">

  <section class="card card--back" aria-label="Card back">
    <svg class="card__art" viewBox="0 0 700 400" role="img" aria-label="Large blue emblem area rising off the left edge">
      <defs>
        <linearGradient id="emblemBack" x1="0" y1="0" x2="0" y2="1">
          <stop offset="0" stop-color="#45b8f5"/>
          <stop offset="1" stop-color="#1763e0"/>
        </linearGradient>
      </defs>
      <circle cx="20" cy="250" r="210" fill="url(#emblemBack)"/>
    </svg>
    <div class="brand">
      <div class="wordmark"><span class="wordmark__dot"></span>LARKSPUR TALENT</div>
      <p class="tagline">Building teams that ship</p>
    </div>
    <p class="website">www.larkspurtalent.example</p>
    <ul class="socials">
      <li>Myriada</li>
      <li>Blipster</li>
      <li>Careerloop</li>
    </ul>
  </section>

  <section class="card card--front" aria-label="Card front">
    <svg class="card__art" viewBox="0 0 700 400" role="img" aria-label="Large blue emblem area and faint watermark circle">
      <defs>
        <linearGradient id="emblemFront" x1="0" y1="0" x2="0" y2="1">
          <stop offset="0" stop-color="#45b8f5"/>
          <stop offset="1" stop-color="#1763e0"/>
        </linearGradient>
      </defs>
      <circle cx="300" cy="230" r="190" fill="#ebebeb"/>
      <circle cx="670" cy="120" r="160" fill="url(#emblemFront)"/>
    </svg>
    <div class="brand">
      <div class="wordmark"><span class="wordmark__dot"></span>LARKSPUR TALENT</div>
      <p class="tagline">Building teams that ship</p>
    </div>
    <div class="contact">
      <p class="contact__name">Jordan Reyes</p>
      <p class="contact__title">Designation</p>
      <ul class="contact__lines">
        <li>555 014-2287
          <svg viewBox="0 0 16 16" aria-label="Office phone"><path d="M3 1h3l1 4-2 1a9 9 0 0 0 5 5l1-2 4 1v3c0 1-1 2-2 2A13 13 0 0 1 1 3c0-1 1-2 2-2z"/></svg>
        </li>
        <li>555 014-2288
          <svg viewBox="0 0 16 16" aria-label="Mobile"><path d="M4 0h8a1 1 0 0 1 1 1v14a1 1 0 0 1-1 1H4a1 1 0 0 1-1-1V1a1 1 0 0 1 1-1zm1 2v10h6V2z"/></svg>
        </li>
        <li class="email">info@larkspurtalent.example
          <svg viewBox="0 0 16 16" aria-label="Email"><path d="M1 3h14v10H1zm1 1 6 5 6-5z"/></svg>
        </li>
      </ul>
    </div>
  </section>

</main>
</body>
</html>
```